Flyer-Design für psychologische Beratungspraxis für Mütter
Vielen herzlichen Dank! Super Kommunikation, alle Änderungswünsche wurden sofort umgesetzt, auch hin und her meinerseits war kein Problem, immer wieder. Schnelle Reaktion, tolle Ideen. Ich bin super zufrieden und würde jederzeit sehr gerne wieder mit brightfoxes zusammenarbeiten! Toller Flyer, ich liebe meinen neuen Flyer! :)
Zielgruppe
Gelassenheitswerkstatt ist eine psychologische Beratungspraxis. Ich unterstütze Mütter, Schwangere und Frauen mit Kinderwunsch bei Herausforderungen rund um Schwangerschaft, Geburt, Mutterschaft, und damit einhergehenden Problemen.
Aufgabenstellung
Text nochmal geringgradig geändert...siehe Datei anbei

```html
<!DOCTYPE html>
<html lang="de">
<head>
<meta charset="utf-8">
<title>Gelassenheitswerkstatt – Flyer</title>
<link rel="stylesheet" href="https://fonts.googleapis.com/css2?family=Amatic+SC:wght@700&family=Inter:wght@400;700;800&display=swap">
<style>
  :root {
    --backdrop: #ebebe9;
    --navy: #262c8c;
    --navy-soft: #3b43a3;
    --highlight: #a9c3e2;
    --pill: #e9e9ee;
    --page-left: #e3e7e4;
    --page-right: #fbfbfa;
    --warm-dark: #3a2418;
    --warm-mid: #a45a22;
    --warm-light: #e3a867;
    --sky: #a9c0d6;
  }
  * { box-sizing: border-box; margin: 0; padding: 0; }
  html, body { width: 1200px; height: 864px; overflow: hidden; }
  body {
    background: var(--backdrop);
    font-family: "Inter", Arial, sans-serif;
    color: var(--navy);
    position: relative;
  }
  .page {
    position: absolute;
    top: 247px;
    width: 370px;
    height: 370px;
    overflow: hidden;
    box-shadow: 0 6px 18px rgba(0,0,0,.12);
  }
  .page--intro { left: 30px; background: var(--page-left); padding: 26px 22px 20px 26px; }
  .page--offer { left: 400px; background: var(--page-right); padding: 26px 24px 20px 26px; }
  .page--cover { left: 800px; }
  .fold { position: absolute; top: 247px; left: 400px; width: 1px; height: 370px; background: rgba(0,0,0,.08); }

  .copy { font-size: 8.2px; line-height: 1.42; }
  .copy p { margin-bottom: 6px; }
  .copy strong { font-weight: 800; }
  .mark {
    background: var(--highlight);
    border-radius: 6px;
    padding: 0 3px;
    font-weight: 800;
  }

  .intro-photo {
    float: right;
    width: 132px;
    height: 122px;
    margin: 0 -8px 6px 8px;
    shape-outside: ellipse(50% 50%);
  }
  .intro-photo svg { display: block; }

  .heading {
    display: inline-block;
    background: var(--pill);
    border-radius: 12px;
    padding: 3px 14px 3px 10px;
    font-weight: 800;
    font-size: 17px;
    letter-spacing: 1px;
    margin-bottom: 10px;
  }
  .list { list-style: none; margin-bottom: 8px; }
  .list li { padding-left: 2px; }
  .offer-photo { position: absolute; right: 16px; bottom: 12px; }

  .cover-photo { position: absolute; inset: 0; }
  .cover-title {
    position: absolute;
    top: 34px; right: 22px;
    display: flex; flex-direction: column; align-items: flex-end; gap: 5px;
    font-family: "Amatic SC", cursive;
    font-weight: 700;
    font-size: 22px;
    letter-spacing: .5px;
    line-height: 1;
  }
  .cover-title span {
    background: rgba(236,236,242,.93);
    border-radius: 14px;
    padding: 2px 12px 1px;
    color: var(--navy);
  }
  .brand {
    position: absolute; right: 22px; bottom: 20px;
    display: flex; align-items: center; gap: 6px;
    font-family: "Inter", Arial, sans-serif;
    font-size: 9px; font-weight: 400;
    color: #f4ece2; letter-spacing: .5px;
  }
  .brand-dot { width: 12px; height: 12px; border-radius: 50%; border: 1.5px solid #f4ece2; }
</style>
</head>
<body>

  <section class="page page--intro copy">
    <div class="intro-photo">
      <svg width="132" height="122" viewBox="0 0 132 122" role="img" aria-label="Foto: Mutter trägt ihr Kind auf dem Arm vor hellem Himmel">
        <defs>
          <linearGradient id="skyFill" x1="0" y1="0" x2="1" y2="1">
            <stop offset="0" stop-color="#b9cde0"/>
            <stop offset=".55" stop-color="#7d6a5a"/>
            <stop offset="1" stop-color="#c8b79a"/>
          </linearGradient>
        </defs>
        <path d="M20 30 C40 5 100 2 122 40 C134 70 112 112 70 116 C30 120 4 96 8 64 C10 48 12 40 20 30Z" fill="url(#skyFill)"/>
        <path d="M118 4 C112 20 112 26 114 32" fill="none" stroke="var(--navy)" stroke-width="1.4"/>
      </svg>
    </div>
    <p><strong>Mutter sein ist wunderbar.</strong> Wenn eine Frau Mutter wird, ist sie plötzlich verliebt über beide Ohren, unbändig stolz und von Glücksgefühlen völlig überwältigt. <strong>So ist es doch NORMAL, oder..?</strong></p>
    <p><strong>Überforderung, Frustration</strong> und <strong>Verzweiflung</strong> kennen Mütter, Frauen mit Kinderwunsch und werdende Mütter allerdings ebenfalls nur zu gut. Wichtig ist, dass die Beurteilung einer Situation, d.h. wie stark sie uns belastet alleine uns selbst zusteht. Nur unsere eigene <strong>subjektive Einschätzung</strong> ist ausschlaggebend.</p>
    <p>So unterschiedlich wir Menschen sind, so verschieden ist auch unser persönliches Fühlen und Erleben. Deshalb benötigen wir <strong>individuell passende Lösungen</strong> für unsere Herausforderungen.</p>
    <p>Ja, Mutter sein ist wundervoll! Und ja, die Dynamik der Paarbeziehung verändert sich schlagartig und wir stehen plötzlich vor einer der erfüllendsten Aufgaben und zugleich einer der größten <strong>existentiellen Herausforderungen</strong> die uns das Leben bietet: <span class="mark">Eltern sein.</span></p>
  </section>

  <section class="page page--offer copy">
    <h2 class="heading">WENN ALSO…</h2>
    <ul class="list">
      <li>… wir <strong>gern Mutter wären</strong> aber das Leben andere Pläne hat?</li>
      <li>… uns die Erfahrung der <strong>Geburt belastet,</strong> aber niemand zuhört weil ja „jetzt alles ok ist“?</li>
      <li>… wenn wir unser <strong>Kind verloren</strong> haben?</li>
      <li>… unser Kind oder wir selbst mit einer <strong>Krankheit</strong> zu kämpfen haben?</li>
      <li>… wir selbst oder unser Partner uns <strong>kaum wiedererkennen?</strong></li>
      <li>… wenn wir uns treu bleiben wollen aber uns dennoch durch die Meinung anderer <strong>verunsichern</strong> lassen?</li>
      <li>… wir eben <strong>nicht stolz</strong> darauf sind wie wir den letzten Schreianfall unseres Babys begleitet haben?</li>
      <li>… wir weder die Wut unseres Kindes, noch unsere eigene <strong>Wut</strong> gebändigt bekommen?</li>
      <li>… wir mit der Situation <strong>überfordert</strong> sind und nicht mehr weiter wissen?</li>
    </ul>
    <p>Um trotz Rückschlägen ein zufriedenes Leben zu führen und um feinfühlig für unsere Kinder da zu sein, benötigen wir viel Kraft. Mentale Kraft, die es uns ermöglicht aus den Augen unserer Kinder zu sehen, unsere eigenen Gefühle zu regulieren und die starken Gefühle unserer Kinder auszuhalten und zu begleiten.</p>
    <p style="width:250px">Gemeinsam erarbeiten wir <span class="mark">individuelle Strategien,</span> wie Sie auf Ihre eigenen Ressourcen besser zugreifen, und so mental gestärkt nach vorne schauen können.</p>
    <svg class="offer-photo" width="96" height="90" viewBox="0 0 96 90" role="img" aria-label="Foto: kleine Babyhand hält einen Finger">
      <defs>
        <radialGradient id="skinFill" cx=".35" cy=".55" r=".7">
          <stop offset="0" stop-color="#e9b7a2"/>
          <stop offset=".6" stop-color="#f1ece8"/>
          <stop offset="1" stop-color="#f5f4f2"/>
        </radialGradient>
      </defs>
      <circle cx="46" cy="48" r="40" fill="url(#skinFill)"/>
      <path d="M56 14 C68 4 84 4 94 8" fill="none" stroke="var(--navy)" stroke-width="1.4"/>
    </svg>
  </section>
  <div class="fold"></div>

  <section class="page page--cover">
    <svg class="cover-photo" width="370" height="370" viewBox="0 0 370 370" role="img" aria-label="Foto: Mutter umarmt ihr Kind im warmen Abendlicht auf einem Feld">
      <defs>
        <linearGradient id="warmFill" x1="0" y1="0" x2="1" y2="1">
          <stop offset="0" stop-color="#d8d2cb"/>
          <stop offset=".25" stop-color="var(--warm-light)"/>
          <stop offset=".55" stop-color="var(--warm-mid)"/>
          <stop offset="1" stop-color="var(--warm-dark)"/>
        </linearGradient>
      </defs>
      <rect width="370" height="370" fill="url(#warmFill)"/>
    </svg>
    <h1 class="cover-title">
      <span>Krisenbegleitung und Lebensberatung</span>
      <span>für Mütter, Schwangere</span>
      <span>und Frauen mit Kinderwunsch</span>
    </h1>
    <div class="brand"><span class="brand-dot"></span>Gelassenheitswerkstatt</div>
  </section>

</body>
</html>
```